Redesign of business card for Cedar Ridge Mechanical

We are looking for a new design for our business cards for Cedar Ridge Mechanical. We are a plumbing & HVAC construction company, operating on the West Coast of Canada and USA. Logo attached.
Industry/Entity Type
Construction - Plumbing & HVAC
Contact Information for Business Card
Name, address, phone numbers, email, website address
Look and feel
Each slider illustrates characteristics of the customer's brand and the style your logo design should communicate.

```html
<!DOCTYPE html>
<html lang="en">
<head>
<meta charset="UTF-8">
<title>Cedar Ridge Mechanical – Business Card</title>
<link rel="stylesheet" href="https://fonts.googleapis.com/css2?family=Poppins:wght@300;400;600&display=swap">
<style>
  :root {
    --backdrop: #222223;
    --card-black: #1c1c1e;
    --paper-white: #ffffff;
    --ink-light: #f2f2f2;
    --ink-dark: #1a1a1a;
  }
  * { margin: 0; padding: 0; box-sizing: border-box; }
  html, body { width: 1200px; height: 780px; overflow: hidden; background: var(--backdrop); }
  body { font-family: "Poppins", sans-serif; position: relative; }

  .card {
    position: absolute;
    top: 240px;
    width: 525px;
    height: 300px;
    background: var(--card-black);
    overflow: hidden;
  }
  .card--front { left: 50px; }
  .card--back { left: 625px; display: flex; align-items: center; justify-content: center; }

  .front-swoosh { position: absolute; inset: 0; width: 100%; height: 100%; }

  .holder { position: absolute; left: 40px; top: 36px; color: var(--ink-light); }
  .holder-name { font-size: 25px; line-height: 1.1; font-weight: 300; }
  .holder-name strong { font-weight: 600; }
  .holder-title { font-size: 12px; font-weight: 300; margin-top: 4px; padding-left: 70px; }

  .brand-name {
    font-family: "Poppins", sans-serif;
    font-weight: 600;
    color: var(--ink-light);
    text-transform: uppercase;
    letter-spacing: 1px;
    display: flex;
    align-items: center;
    gap: 10px;
  }
  .brand-name .brand-square { width: 14px; height: 14px; background: var(--ink-light); flex: none; }
  .card--front .brand-name { position: absolute; left: 285px; top: 44px; font-size: 15px; line-height: 1.25; }
  .card--back .brand-name { font-size: 28px; line-height: 1.25; gap: 16px; }
  .card--back .brand-name .brand-square { width: 24px; height: 24px; }

  .divider { position: absolute; left: 250px; top: 120px; width: 1.5px; height: 70px; background: var(--ink-light); }

  .contact-list { position: absolute; left: 270px; top: 122px; list-style: none; color: var(--ink-light); font-size: 13px; font-weight: 300; }
  .contact-list li { display: flex; align-items: center; gap: 9px; height: 22px; }
  .contact-list svg { width: 13px; height: 13px; flex: none; }

  .address { position: absolute; left: 40px; bottom: 26px; color: var(--ink-dark); font-size: 12.5px; font-weight: 400; }
</style>
</head>
<body>

<section class="card card--front">
  <svg class="front-swoosh" viewBox="0 0 525 300" preserveAspectRatio="none" aria-hidden="true">
    <path d="M0 215 C 150 215, 300 250, 380 300 L 0 300 Z" fill="var(--paper-white)"/>
    <path d="M0 300 L0 196 C 160 196, 330 225, 525 255 L525 300 Z" fill="var(--paper-white)"/>
    <path d="M20 208 C 170 212, 330 240, 470 262" fill="none" stroke="var(--card-black)" stroke-width="2.5"/>
    <path d="M0 232 C 160 234, 290 260, 360 300" fill="none" stroke="none"/>
  </svg>

  <div class="holder">
    <p class="holder-name"><strong>Marta</strong> Kovalska</p>
    <p class="holder-title">Founder &amp; CEO</p>
  </div>

  <p class="brand-name"><span class="brand-square"></span><span>Cedar Ridge<br>Mechanical</span></p>

  <span class="divider"></span>

  <ul class="contact-list">
    <li>
      <svg viewBox="0 0 24 24" aria-hidden="true"><path fill="currentColor" d="M6.6 10.8a15.1 15.1 0 0 0 6.6 6.6l2.2-2.2c.3-.3.7-.4 1-.2 1.1.4 2.3.6 3.6.6.6 0 1 .4 1 1V20c0 .6-.4 1-1 1A17 17 0 0 1 3 4c0-.6.4-1 1-1h3.5c.6 0 1 .4 1 1 0 1.3.2 2.5.6 3.6.1.3 0 .7-.2 1z"/></svg>
      (555) 214-3870
    </li>
    <li>
      <svg viewBox="0 0 24 24" aria-hidden="true"><circle cx="12" cy="12" r="9" fill="none" stroke="currentColor" stroke-width="2"/><path d="M3 12h18M12 3c3 3 3 15 0 18M12 3c-3 3-3 15 0 18" fill="none" stroke="currentColor" stroke-width="1.6"/></svg>
      info@cedarridgemech.com
    </li>
    <li>
      <svg viewBox="0 0 24 24" aria-hidden="true"><rect x="3" y="6" width="18" height="13" rx="1.5" fill="none" stroke="currentColor" stroke-width="2"/><path d="M3 7l9 7 9-7" fill="none" stroke="currentColor" stroke-width="2"/></svg>
      www.cedarridgemech.com
    </li>
  </ul>

  <p class="address">1840 Harbor Ln. Suite 300 Bellingham, WA 98225</p>
</section>

<section class="card card--back">
  <p class="brand-name"><span class="brand-square"></span><span>Cedar Ridge<br>Mechanical</span></p>
</section>

</body>
</html>
```